Security and Technology Website - Bold and Confident, Something Unexpected

Maple Wren Systems is launching its first website and we need a great design to bring our brand to life and generate DTC and B2B leads.

We have a good logo, but I am struggling with the creative vision to bring it all together. While our industry is Alarm Systems and Technology, we want to create a site that is more friendly and less 'typical' than your standard IT sites.

It Must:
1. Appeal to both men and women. The logo is a bit masculine, so the colors and icons must soften this.
2. Feel modern - we need to convey that we we use the latest technology.
3. Feel a bit high-end. We are not a budget solution.
4. Have a distinct iconography and photo treatment.
5. Feel layered - not just a series of stacked horizontal modules.

It Should Not:
1. Feel like your typical IT website.

Here are resources to get you started!
• Staging Site:
https://maple-wren-systems.shopfrontdemo.example/
Password: Piper

•Brand Guide: https://www.layoutboard.example/design/QKRmWpLcT4V/hNbq8Yf2-ZsKeRtDw7xp-QE/edit?utm_content=QKRmWpLcT4V&utm_campaign=designshare&utm_medium=link2&utm_source=sharebutton

• Logo and Fonts and Photos: :https://files.cloudlocker.example/folders/7HtPqWmZc3Kd9RbLx2VnYs8FgJe4UoAiT?usp=sharing

• Design Inspiration (don't feel limited by this): https://www.layoutboard.example/design/QKTnHsVbWe8/p7MfRz31xYqLcKdTu9GNBw/edit?utm_content=QKTnHsVbWe8&utm_campaign=designshare&utm_medium=link2&utm_source=sharebutton

______________

The winner will be asked to provide design files and finished PNGs of the overall design file, backgrounds, photo treatments/frames, and icons.

The winner will likely be engaged for a phase 2 to build out a product page.

Industry/Entity Type

Alarm Systems, Home Theatres, and Commercial IT Networking

Number of Pages Required

1 page

Font styles to use
Sans Serif

Colors
0054AA
0677BA
7BADD7
CADEEF
E8F1F8
0094D4
00A9DD
6FCCEA
C7EBF8
E9F6FB
EB3D1F
EC4F4E
F09395
F8D3D4
FCEDEE

Requirements
Must have
• 1. Appeal to both men and women. The logo is a bit masculine, so the colors and icons must soften this. 2. Feel modern - we need to convey that we we use the latest technology. 3. Feel a bit high-end. We are not a budget solution. 4. Have a distinct iconography and photo treatment. 5. Feel layered - not just a series of stacked horizontal modules.
Should not have
• 1. Should not feel like just another IT website.

```html
<!DOCTYPE html>
<html lang="en">
<head>
<meta charset="utf-8">
<title>Maple Wren Systems – Safer. Smarter. Faster.</title>
<link href="https://fonts.googleapis.com/css2?family=Russo+One&family=Poppins:wght@400;500;600;700&display=swap" rel="stylesheet">
<style>
:root{
  --red:#d10a14;
  --red-dark:#b8000c;
  --blue:#2463b8;
  --blue-deep:#1a4f9c;
  --navy:#0b1a3a;
  --grey:#8c8c8c;
  --ink:#1a1a1a;
  --body:#333;
  --white:#fff;
  --magenta:#e23fc5;
  --green:#8dc63f;
  --orange:#f7941d;
  --teal:#1fb5b5;
  --purple:#6b2c7f;
}
*{margin:0;padding:0;box-sizing:border-box}
html,body{width:1200px;height:5277px;overflow:hidden}
body{font-family:'Poppins',sans-serif;color:var(--body);background:var(--white);position:relative}
.page{position:relative;width:1200px;height:5277px;overflow:hidden}
.abs{position:absolute}
.display{font-family:'Russo One',sans-serif;text-transform:uppercase;color:var(--ink)}
.btn{position:absolute;background:var(--red);color:#fff;font-weight:700;font-size:15px;display:flex;align-items:center;justify-content:center;text-transform:uppercase;letter-spacing:.3px}
.btn.sm{font-size:15px;text-transform:none}

/* top bar */
.topbar{left:0;top:0;width:1200px;height:41px;background:var(--red)}
.topbar .cta{left:150px;top:11px;color:#fff;font-size:13px;font-weight:700}
.topbar .social{top:10px;width:21px;height:21px;border-radius:50%}
.nav{left:0;top:41px;width:1200px;height:65px;background:#fff}
.nav ul{position:absolute;left:365px;top:24px;display:flex;gap:28px;list-style:none;font-size:15px;color:#333}
.nav li.active{color:var(--red)}
.brand-badge{left:150px;top:36px;width:140px;height:140px;border-radius:50%;background:#fff;z-index:5;box-shadow:0 4px 10px rgba(0,0,0,.15);display:flex;align-items:center;justify-content:center;flex-direction:column;text-align:center}
.brand-badge span{font-family:'Russo One',sans-serif;color:var(--blue);font-size:17px;line-height:1.1}

/* hero */
.hero{left:0;top:106px;width:1200px;height:484px;background:linear-gradient(90deg,#6f7f8a 0%,#4c6a8c 35%,#2f66b6 55%,var(--blue) 100%)}
.hero .kicker{left:680px;top:137px;color:#fff;font-size:15px;letter-spacing:.3px}
.hero h1{left:678px;top:160px;color:#fff;font-size:41px;line-height:48px;font-weight:400}
.hero .sub{left:682px;top:258px;color:#fff;font-family:'Russo One',sans-serif;font-size:15px}
.hero .arrow{top:386px;width:33px;height:33px;background:var(--red);display:flex;align-items:center;justify-content:center}

/* about */
.about-title{left:145px;top:662px;font-size:40px}
.about-lead{left:145px;top:712px;width:430px;color:var(--blue);font-family:'Russo One',sans-serif;font-size:18px;line-height:26px;text-transform:uppercase}
.about-copy{left:145px;top:800px;width:440px;font-size:13.5px;line-height:21px;color:#333}
.about-copy p{margin-bottom:15px}
.about-photo{left:698px;top:672px;width:349px;height:360px;border-radius:8px;background:linear-gradient(160deg,#6f7276,#3c3f44 60%,#23262c)}

/* services */
.services{left:0;top:1116px;width:1200px;height:690px;background:var(--navy)}
.services h2{left:0;width:1200px;text-align:center;top:70px;color:#fff;font-size:40px}
.card{position:absolute;background:#fff;border-radius:8px;padding:12px}
.card .ph{width:100%;height:100%;border-radius:8px;display:flex;align-items:center;justify-content:center;color:#fff;font-family:'Russo One',sans-serif;font-size:18px;text-transform:uppercase;text-align:center}

/* diagram */
.diagram{left:0;top:1806px;width:1200px;height:805px}
.node{position:absolute;border-radius:50%;background:#fff;text-align:center;display:flex;flex-direction:column;align-items:center;justify-content:center;padding:0 30px}
.node h4{font-family:'Poppins',sans-serif;font-weight:700;font-size:12.5px;line-height:15px;color:var(--ink);text-transform:uppercase;margin-top:4px}
.node p{font-size:9px;line-height:12px;color:#444;margin-top:4px}

/* steps */
.steps{left:0;top:2611px;width:1200px;height:549px;background:var(--blue)}
.steps h2{left:0;width:1200px;text-align:center;top:73px;color:#fff;font-size:40px;line-height:50px}
.step{position:absolute;top:215px;width:283px;height:250px;background:#fff;text-align:center;padding:88px 22px 0}
.step .num{position:absolute;left:0;top:-22px;width:106px;height:106px;border-radius:50%;background:var(--red);color:#fff;font-family:'Russo One',sans-serif;font-size:28px;display:flex;align-items:center;justify-content:center;border:5px solid #fff}
.step h3{font-weight:700;font-size:15px;color:var(--ink);text-transform:uppercase;letter-spacing:.3px}
.step p{font-size:13px;line-height:20px;margin-top:12px;color:#444}
.step a{display:block;margin-top:14px;font-weight:700;font-size:14px;color:var(--ink);text-decoration:underline}

/* reviews */
.reviews{left:0;top:3160px;width:1200px;height:573px;background:var(--red)}
.reviews h2{left:0;width:1200px;text-align:center;top:72px;color:#fff;font-size:40px}
.review{position:absolute;top:145px;height:330px;border:1px solid rgba(255,255,255,.8);border-radius:8px;text-align:center;color:#fff;padding:40px 32px}
.review .who{font-weight:700;font-size:13px}
.review .stars{color:#f7c948;font-size:15px;letter-spacing:1px;margin:6px 0 10px}
.review p{font-size:14px;line-height:22px}

/* partners */
.partners{left:0;top:3733px;width:1200px;height:336px;background:var(--grey)}
.partners h2{left:0;width:1200px;text-align:center;top:80px;color:#fff;font-size:40px}
.partner{position:absolute;top:144px;width:178px;height:96px;background:#fff;border-radius:4px;display:flex;align-items:center;justify-content:center}
.partner i{display:block;width:96px;height:34px;border-radius:4px;background:#d6d9de}

/* quote */
.monitor-top{left:152px;top:4149px;width:387px;height:221px;background:var(--red);color:#fff;display:flex;align-items:center;justify-content:center;text-align:center;font-size:40px;line-height:48px}
.monitor-bottom{left:152px;top:4370px;width:387px;height:246px;background:var(--blue);color:#fff;text-align:center;padding:30px 46px 0;font-size:14px;line-height:22px}
.quote-title{left:600px;top:4140px;font-size:40px}
.field{position:absolute;border:1px solid #555;background:#fff}
.label{position:absolute;font-size:14px;color:#333}

/* newsletter + footer */
.footer{left:0;top:4809px;width:1200px;height:468px;background:var(--navy)}
.newsletter{left:145px;top:4710px;width:910px;height:144px;background:var(--red);z-index:3}
.newsletter h3{position:absolute;left:45px;top:48px;color:#fff;font-size:23px}
.newsletter p{position:absolute;left:45px;top:82px;color:#fff;font-size:13.5px}
.newsletter .email{position:absolute;left:528px;top:58px;width:218px;height:40px;border:1px solid #fff;color:#fff;font-size:11px;padding:12px 14px}
.newsletter .go{position:absolute;left:752px;top:58px;width:108px;height:40px;background:var(--blue);color:#fff;font-weight:700;font-size:15px;display:flex;align-items:center;justify-content:center}
.fcol{position:absolute;color:#fff;font-size:13px}
.fcol h5{font-weight:700;font-size:13.5px;text-transform:uppercase;line-height:20px;margin-bottom:16px}
.fcol li{list-style:none;position:relative;padding-left:30px;height:36px}
.fcol li::before{content:"";position:absolute;left:0;top:6px;width:11px;height:11px;border-radius:50%;background:var(--red)}
.copy{left:0;width:1200px;top:5225px;text-align:center;color:#fff;font-size:13px}
</style>
</head>
<body>
<div class="page">

  <!-- Header -->
  <div class="abs topbar">
    <div class="abs cta">CONTACT US FOR A QUOTE 615.555.0142</div>
    <svg class="abs" style="left:964px;top:11px" width="19" height="19" viewBox="0 0 20 20"><circle cx="8" cy="8" r="6" fill="none" stroke="#fff" stroke-width="2.5"/><path d="M12.5 12.5 18 18" stroke="#fff" stroke-width="2.5"/></svg>
    <span class="abs social" style="left:1015px;background:var(--blue)"></span>
    <span class="abs social" style="left:1047px;background:var(--blue-deep);border-radius:3px"></span>
  </div>
  <nav class="abs nav">
    <ul>
      <li class="active">Home</li><li>About</li><li>Electronic Security</li><li>Networking</li><li>Cabling</li><li>Project Consulting</li><li>Contact</li>
    </ul>
  </nav>
  <div class="abs brand-badge"><span>Maple Wren<br>Systems</span></div>

  <!-- Hero -->
  <section class="abs hero" role="img" aria-label="Woman on a video call with colleagues at a desktop monitor in a bright home office">
    <div class="abs kicker">PROUDLY SERVING MIDDLE TENNESSEE</div>
    <h1 class="abs display">Safer. Smarter.<br>Faster.</h1>
    <div class="abs sub">HOMES + BUSINESSES</div>
    <div class="btn" style="left:682px;top:293px;width:164px;height:42px">Get Strated</div>
    <div class="abs arrow" style="left:975px"><svg width="12" height="12" viewBox="0 0 12 12"><path d="M8 1 3 6l5 5" fill="none" stroke="#fff" stroke-width="2.4"/></svg></div>
    <div class="abs arrow" style="left:1012px"><svg width="12" height="12" viewBox="0 0 12 12"><path d="m4 1 5 5-5 5" fill="none" stroke="#fff" stroke-width="2.4"/></svg></div>
  </section>

  <!-- About -->
  <h2 class="abs display about-title">About Us</h2>
  <div class="abs about-lead">I founded Maple Wren Systems to bring together technology and honest, reliable service.</div>
  <div class="abs about-copy">
    <p>I'm proud to call Tennessee home and even prouder to help keep its homes and businesses secure.</p>
    <p>Whether it's protecting or elevating your space, my goal is to make technology work for you.</p>
    <p>Think of us as your friendly, neighborhood tech expert—here to safeguard what matters most.</p>
  </div>
  <div class="abs" role="img" aria-label="Founder signature, Elliot Marsh" style="left:145px;top:978px;width:120px;height:56px;background:linear-gradient(90deg,rgba(36,99,184,.15),rgba(36,99,184,.05));border-radius:6px"></div>
  <div class="btn" style="left:293px;top:990px;width:285px;height:42px;font-size:14px">Tell Us How We Can Help</div>
  <div class="abs about-photo" role="img" aria-label="Portrait of the founder in a suit and bow tie"></div>

  <!-- Services -->
  <section class="abs services">
    <h2 class="abs display">Our Services</h2>
    <div class="card" style="left:154px;top:141px;width:532px;height:459px">
      <div class="ph" role="img" aria-label="Woman using a wall-mounted security touch panel" style="background:linear-gradient(135deg,#c9b49a,#8a6f58 55%,#4d3b30)">Affordable Security</div>
    </div>
    <div class="card" style="left:698px;top:141px;width:353px;height:252px">
      <div class="ph" role="img" aria-label="Home theatre room with a large screen" style="background:linear-gradient(135deg,#6a5a48,#3a3129 60%,#c59a4a)">Enviable Entertainment</div>
    </div>
    <div class="card" style="left:698px;top:404px;width:353px;height:196px">
      <div class="ph" role="img" aria-label="Business team in a video conference meeting" style="background:linear-gradient(135deg,#7d8896,#4b5563 60%,#2c3440)">Connected Businesses</div>
    </div>
  </section>

  <!-- Feature diagram -->
  <section class="abs diagram">
    <svg class="abs" style="left:0;top:0" width="1200" height="805" viewBox="0 0 1200 805">
      <circle cx="608" cy="529" r="190" fill="none" stroke="var(--red)" stroke-width="3"/>
      <line x1="604" y1="258" x2="608" y2="344" stroke="var(--magenta)" stroke-width="4"/>
      <line x1="380" y1="324" x2="467" y2="402" stroke="var(--green)" stroke-width="4"/>
      <line x1="830" y1="324" x2="745" y2="402" stroke="var(--orange)" stroke-width="4"/>
      <line x1="320" y1="539" x2="418" y2="539" stroke="var(--teal)" stroke-width="4"/>
      <line x1="883" y1="535" x2="799" y2="539" stroke="var(--purple)" stroke-width="4"/>
      <circle cx="608" cy="344" r="19" fill="var(--magenta)"/>
      <circle cx="467" cy="402" r="19" fill="var(--green)"/>
      <circle cx="745" cy="402" r="19" fill="var(--orange)"/>
      <circle cx="418" cy="539" r="19" fill="var(--teal)"/>
      <circle cx="799" cy="539" r="19" fill="var(--purple)"/>
      <circle cx="608" cy="529" r="143" fill="var(--blue)" stroke="#fff" stroke-width="6"/>
      <circle cx="604" cy="170" r="84" fill="#fff" stroke="var(--magenta)" stroke-width="8"/>
      <circle cx="334" cy="283" r="84" fill="#fff" stroke="var(--green)" stroke-width="8"/>
      <circle cx="877" cy="283" r="84" fill="#fff" stroke="var(--orange)" stroke-width="8"/>
      <circle cx="238" cy="539" r="84" fill="#fff" stroke="var(--teal)" stroke-width="8"/>
      <circle cx="965" cy="535" r="84" fill="#fff" stroke="var(--purple)" stroke-width="8"/>
      <g fill="none" stroke="var(--red)" stroke-width="2">
        <rect x="589" y="114" width="30" height="6"/><circle cx="604" cy="130" r="10"/><circle cx="604" cy="130" r="4"/>
        <rect x="325" y="212" width="18" height="30" rx="2"/><circle cx="334" cy="222" r="4"/><circle cx="334" cy="235" r="2"/>
        <circle cx="877" cy="228" r="6"/><circle cx="866" cy="217" r="3.5"/><circle cx="888" cy="217" r="3.5"/><circle cx="862" cy="228" r="3"/><circle cx="892" cy="228" r="3"/>
        <circle cx="238" cy="478" r="4"/><path d="M228 468a14 14 0 0 0 0 20M248 468a14 14 0 0 1 0 20M222 462a22 22 0 0 0 0 32M254 462a22 22 0 0 1 0 32"/>
        <path d="M965 465c10 10 12 18 6 26-3 4-12 4-15 0-5-7-1-12 3-16 0 6 3 6 4 4 2-4-1-9 2-14z"/>
      </g>
    </svg>
    <div class="node" style="left:520px;top:86px;width:168px;height:168px;padding-top:38px"><h4>Security<br>Cameras</h4><p>Pair text with an icon to focus on your chosen product, collection, or blog post.</p></div>
    <div class="node" style="left:250px;top:199px;width:168px;height:168px;padding-top:38px"><h4>Video<br>Doorbells</h4><p>Pair text with an icon to focus on your chosen product, collection, or blog post.</p></div>
    <div class="node" style="left:793px;top:199px;width:168px;height:168px;padding-top:38px"><h4>Pet-<br>Friendly</h4><p>Pair text with an icon to focus on your chosen product, collection, or blog post.</p></div>
    <div class="node" style="left:154px;top:455px;width:168px;height:168px;padding:38px 22px 0"><h4>Entry &amp; Motion<br>Sensors</h4><p>Pair text with an icon to focus on your chosen product, collection, or blog post.</p></div>
    <div class="node" style="left:881px;top:451px;width:168px;height:168px;padding:38px 22px 0"><h4>Fire &amp; Carbon<br>Monoxide</h4><p>Pair text with an icon to focus on your chosen product, collection, or blog post.</p></div>
    <div class="abs" style="left:478px;top:430px;width:260px;text-align:center;color:#fff">
      <div class="display" style="color:#fff;font-size:27px;line-height:34px">Connect +<br>Protect<br>Your<br>World</div>
      <div style="font-size:12.5px;line-height:19px;margin-top:12px;padding:0 18px">Protect your people, assets, and information from whatever comes.</div>
    </div>
  </section>

  <!-- Steps -->
  <section class="abs steps">
    <h2 class="abs display">A Safer Home or Business is<br>as Easy as 1-2-3</h2>
    <div class="step" style="left:145px"><div class="num">01</div><h3>Build an Instant Quote</h3><p>Our live-estimate builder will guide you through a few questions to help us understand your needs.</p><a>Get Started</a></div>
    <div class="step" style="left:459px"><div class="num">02</div><h3>Schedule Installation</h3><p>Our trained techs are efficient and friendly. Southern-born and raised, we will respect your home and your schedule.</p><a>Get Started</a></div>
    <div class="step" style="left:772px"><div class="num">03</div><h3>Stay Secure 24/7</h3><p>Monitor your home through the app, receive instant alerts, and rely on professional monitoring services for emergencies.</p><a>Get Started</a></div>
  </section>

  <!-- Reviews -->
  <section class="abs reviews">
    <h2 class="abs display" style="color:#fff">Client Reviews</h2>
    <svg class="abs" style="left:58px;top:290px" width="22" height="32" viewBox="0 0 22 32"><path d="M18 3 5 16l13 13" fill="none" stroke="#fff" stroke-width="4"/></svg>
    <svg class="abs" style="left:1110px;top:290px" width="22" height="32" viewBox="0 0 22 32"><path d="m4 3 13 13L4 29" fill="none" stroke="#fff" stroke-width="4"/></svg>
    <div class="review" style="left:145px;width:443px"><div class="who">- Summit Ledger Properties</div><div class="stars">★★★★★</div><p>Fantastic service!! Used Brightline and Homevault in the past, and their customer service does not compare to Maple Wren! Installation and set up went smoothly!! It's so convenient to use the apps remotely for the cameras, and arming or unarming the alarm. I'd rate them more than 5 stars if I was able to!</p></div>
    <div class="review" style="left:618px;width:437px"><div class="who">- Nora K. Cedar Falls, TN</div><div class="stars">★★★★★</div><p>I couldn't be more impressed with the service we received for our condo's security system upgrade. The team was professional, efficient, and incredibly knowledgeable. providing us with state-of-the-art solutions that have significantly enhanced the safety and security of our building. Highly recommend their services!</p></div>
  </section>

  <!-- Partners -->
  <section class="abs partners">
    <h2 class="abs display" style="color:#fff">Service Partners</h2>
    <div class="partner" style="left:143px"><i></i></div>
    <div class="partner" style="left:327px"><i></i></div>
    <div class="partner" style="left:511px"><i></i></div>
    <div class="partner" style="left:695px"><i></i></div>
    <div class="partner" style="left:879px"><i></i></div>
  </section>

  <!-- Monitoring + Quote -->
  <div class="abs display monitor-top" style="color:#fff">24/7<br>Monitoring</div>
  <div class="abs monitor-bottom">Our team is always on guard. With always-on protection, we'll notify you of any suspicious activity. In emergencies, we'll monitor your local police, fire, or EMS.</div>
  <div class="btn sm" style="left:295px;top:4536px;width:102px;height:40px">Submit</div>

  <h2 class="abs display quote-title">Request a Quote</h2>
  <div class="label" style="left:601px;top:4205px">Name</div>
  <div class="field" style="left:601px;top:4229px;width:215px;height:40px"></div>
  <div class="label" style="left:838px;top:4205px">Email</div>
  <div class="field" style="left:838px;top:4229px;width:215px;height:40px"></div>
  <div class="label" style="left:601px;top:4281px">Phone</div>
  <div class="field" style="left:601px;top:4305px;width:452px;height:40px"></div>
  <div class="label" style="left:601px;top:4369px">Message</div>
  <div class="field" style="left:601px;top:4393px;width:452px;height:162px"></div>
  <div class="btn sm" style="left:602px;top:4572px;width:113px;height:42px">Submit</div>

  <!-- Newsletter + Footer -->
  <div class="abs footer"></div>
  <div class="abs newsletter">
    <h3 class="display" style="color:#fff">Subscribe to our Newsletter</h3>
    <p>Security Tips, Special Offers, and More!</p>
    <div class="email">Your email</div>
    <div class="go">Submit</div>
  </div>

  <div class="abs" style="left:160px;top:4950px;width:150px;text-align:center;font-family:'Russo One',sans-serif;color:var(--blue);font-size:21px;line-height:24px">Maple Wren<br>Systems</div>
  <span class="abs" style="left:218px;top:5100px;width:10px;height:16px;background:#fff;border-radius:2px"></span>
  <span class="abs" style="left:236px;top:5100px;width:14px;height:14px;background:var(--red);border-radius:2px"></span>

  <div class="fcol" style="left:367px;top:4934px;width:250px">
    <h5>Proudly Serving Middle<br>Tennessee</h5>
    <div style="display:flex;gap:14px;align-items:flex-start;font-size:12.5px;line-height:17px">
      <svg width="12" height="16" viewBox="0 0 12 16"><path d="M6 0a6 6 0 0 0-6 6c0 4.5 6 10 6 10s6-5.5 6-10a6 6 0 0 0-6-6zm0 8.5A2.5 2.5 0 1 1 6 3.5a2.5 2.5 0 0 1 0 5z" fill="#fff"/></svg>
      <span>482 Harbor Ridge Rd. Suite 2-110<br>Alderbrook, TN 37999</span>
    </div>
    <div style="display:flex;gap:14px;align-items:center;margin-top:20px;font-size:12.5px">
      <svg width="13" height="13" viewBox="0 0 24 24"><path d="M6.6 10.8a15 15 0 0 0 6.6 6.6l2.2-2.2a1 1 0 0 1 1-.25 11.4 11.4 0 0 0 3.6.6 1 1 0 0 1 1 1V20a1 1 0 0 1-1 1A17 17 0 0 1 3 4a1 1 0 0 1 1-1h3.5a1 1 0 0 1 1 1c0 1.250.2 2.450.6 3.6a1 1 0 0 1-.25 1z" fill="#fff"/></svg>
      <span>615.555.0142</span>
    </div>
  </div>
  <div class="btn" style="left:377px;top:5089px;width:188px;height:40px;font-size:14px">Request a Quote</div>

  <div class="fcol" style="left:657px;top:4934px">
    <h5>Residential</h5>
    <ul><li>Home Security</li><li>Smart Homes</li><li>Home Theatres + A/V</li><li>WiFi</li><li>Cabling</li></ul>
  </div>
  <div class="fcol" style="left:881px;top:4934px">
    <h5>Commercial</h5>
    <ul><li>Audio Video</li><li>Cabling</li><li>Communication</li><li>Electronic Security</li><li>Project Consulting</li></ul>
  </div>

  <div class="abs copy">© Copyrights 2024 | All Rights Reserved</div>
</div>
</body>
</html>
```